Full Page Tolver 250 Ad

We need a full page magazine ad. Our company is a site construction company - meaning we build lakes, ponds, do brush clearing for farmers and ranchers. For commercial customers, we build building pads, site clearing, pavement and soil stabilization. The final design should show what we do. Our website is www.pendrowgrading.com

```html
<!DOCTYPE html>
<html lang="en">
<head>
<meta charset="utf-8">
<title>Tolver 250 Full Page Ad – Pendrow Grading</title>
<link rel="stylesheet" href="https://fonts.googleapis.com/css2?family=Anton&family=Montserrat:wght@300;400;600&family=Poppins:wght@400;500;600;700;800&display=swap">
<style>
  :root{
    --yellow:#f6b530;
    --ink:#1f1f1f;
    --dark:#272624;
    --white:#ffffff;
    --red:#e3141b;
    --sky-top:#4f93d6;
    --sky-low:#c4def2;
    --canvas:#c9c9c9;
  }
  *{box-sizing:border-box;margin:0;padding:0}
  html,body{width:1200px;height:2400px;overflow:hidden;background:var(--canvas)}
  .ad{
    position:absolute;left:50px;top:487px;width:1045px;height:1355px;
    transform:scale(1.0526);transform-origin:0 0;
    overflow:hidden;background:var(--dark);
    font-family:'Poppins',sans-serif;color:var(--white);
    box-shadow:0 6px 18px rgba(0,0,0,.35);
  }
  .layer{position:absolute;left:0;top:0}
  .abs{position:absolute}
  .headline{position:absolute;right:64px;text-align:right;white-space:nowrap}
  .kicker{top:58px;font-family:'Montserrat',sans-serif;font-weight:300;font-size:40px;letter-spacing:8px;line-height:1}
  .title{top:92px;font-family:'Anton',sans-serif;font-size:62px;color:var(--yellow);line-height:1.05;letter-spacing:-.5px}
  .subtitle{top:160px;font-weight:800;font-size:44px;line-height:1.1}
  .rule{position:absolute;top:271px;left:470px;width:511px;height:3px;background:var(--yellow)}
  .seg-head{font-weight:800;font-size:32px;line-height:1.02}
  .seg-head .hl{color:var(--yellow)}
  .commercial-head{top:293px;color:var(--white)}
  .farm-head{top:684px;color:var(--ink)}
  .tag{position:absolute;background:var(--yellow);color:var(--ink);font-weight:700;font-size:29px;letter-spacing:3px;text-align:center;line-height:36px}
  .tag-commercial{left:784px;top:369px;width:197px}
  .tag-farm{left:759px;top:759px;width:222px}
  .service{position:absolute;display:flex;align-items:center;gap:14px;font-weight:500;font-size:17px;line-height:1.15}
  .service svg{flex:none}
  .intro{position:absolute;left:150px;top:600px;font-size:17px;line-height:1.25}
  .intro .hl{color:var(--yellow);font-weight:600}
  .farm-item{position:absolute;width:120px;text-align:center;color:var(--ink);font-weight:500;font-size:21px;line-height:1}
  .divider{position:absolute;top:817px;height:120px;border-left:2px dotted #8a8a8a}
  .snap{position:absolute;background:var(--white);padding:6px;box-shadow:0 4px 10px rgba(0,0,0,.35)}
  .snap .shot{width:100%;height:100%}
  .snap .caption{position:absolute;left:6px;bottom:10px;background:rgba(255,255,255,.94);color:var(--ink);font-weight:600;font-size:11px;padding:2px 30px 2px 24px;clip-path:polygon(0 0,90% 0,100% 100%,0 100%)}
  .contact-label{position:absolute;left:56px;top:1237px;border:2px solid var(--ink);color:var(--ink);font-family:'Montserrat',sans-serif;font-size:16px;letter-spacing:5px;padding:0 8px;line-height:19px}
  .phone{position:absolute;left:56px;top:1262px;color:var(--ink);font-weight:700;font-size:26px;display:flex;align-items:center;gap:10px;line-height:32px}
  .estimate{position:absolute;left:318px;top:1238px;font-family:'Montserrat',sans-serif;font-size:17px;letter-spacing:5px}
  .web{position:absolute;left:318px;top:1262px;font-family:'Montserrat',sans-serif;font-size:21px;letter-spacing:3px;display:flex;align-items:center;gap:10px}
  .web .hl{color:var(--yellow);font-weight:600}
  .brand{position:absolute;left:760px;top:1214px;width:222px;display:flex;align-items:center;gap:12px;font-weight:700;font-size:27px;color:var(--white);line-height:1.05}
  .brand .mark{width:32px;height:32px;background:var(--yellow);flex:none}
</style>
</head>
<body>
<div class="ad">
  <svg class="layer" width="1045" height="1355" viewBox="0 0 1045 1355">
    <defs>
      <linearGradient id="sky" x1="0" y1="0" x2="0" y2="1">
        <stop offset="0" stop-color="var(--sky-top)"/><stop offset="1" stop-color="var(--sky-low)"/>
      </linearGradient>
      <radialGradient id="sun" cx="0.5" cy="0.5" r="0.5">
        <stop offset="0" stop-color="#fff" stop-opacity=".95"/><stop offset="1" stop-color="#fff" stop-opacity="0"/>
      </radialGradient>
      <linearGradient id="field" x1="0" y1="0" x2="0" y2="1">
        <stop offset="0" stop-color="#232322"/><stop offset=".5" stop-color="#2e2b27"/><stop offset="1" stop-color="#3a342c"/>
      </linearGradient>
      <linearGradient id="scraper" x1="0" y1="0" x2="1" y2="1">
        <stop offset="0" stop-color="#a8a8a2"/>
        <stop offset=".14" stop-color="#c99a2a"/>
        <stop offset=".45" stop-color="#e0ad34"/>
        <stop offset=".72" stop-color="#a57c22"/>
        <stop offset="1" stop-color="#3a3128"/>
      </linearGradient>
      <linearGradient id="mist" x1="0" y1="0" x2="1" y2="1">
        <stop offset="0" stop-color="#ffffff"/><stop offset=".6" stop-color="#f1f2f2"/><stop offset="1" stop-color="#c9cdd0"/>
      </linearGradient>
      <linearGradient id="dirt" x1="0" y1="0" x2="1" y2="0">
        <stop offset="0" stop-color="#8c7553"/>
        <stop offset=".3" stop-color="#9a7a3c"/>
        <stop offset=".52" stop-color="#7b6a55"/>
        <stop offset=".72" stop-color="#a33632"/>
        <stop offset=".86" stop-color="#7a5040"/>
        <stop offset="1" stop-color="#6b5b48"/>
      </linearGradient>
      <linearGradient id="dirtShade" x1="0" y1="0" x2="0" y2="1">
        <stop offset="0" stop-color="#000" stop-opacity="0"/><stop offset="1" stop-color="#2a2118" stop-opacity=".55"/>
      </linearGradient>
    </defs>

    <rect width="1045" height="1355" fill="url(#field)"/>
    <g role="img" aria-label="Blue sky with bright sun above a dark hillside">
      <path d="M0 0H700L650 35 590 60 520 110 440 150 340 165 240 195 130 205 0 225Z" fill="url(#sky)"/>
      <circle cx="228" cy="40" r="70" fill="url(#sun)"/>
    </g>

    <path d="M0 255 L620 255 L620 640 L300 700 L0 690Z" fill="url(#scraper)" role="img" aria-label="Yellow elevating scraper loaded with dirt beside a rock pile"/>

    <path d="M0 690 L90 684 180 700 1045 700 1045 1355 L0 1355Z" fill="var(--yellow)"/>
    <path d="M258 705 L340 697 430 706 520 694 600 698 680 648 760 638 840 633 920 636 1000 630 1045 628 L1045 1030 L258 1030Z" fill="url(#mist)"/>

    <g role="img" aria-label="Red four-wheel-drive tractor pulling a yellow pull-scraper across bare ground">
      <path d="M258 1017 L1045 1017 L1045 1355 L295 1355 L278 1290 290 1230 268 1160 284 1100 262 1050Z" fill="url(#dirt)"/>
      <path d="M258 1017 L1045 1017 L1045 1355 L295 1355 L278 1290 290 1230 268 1160 284 1100 262 1050Z" fill="url(#dirtShade)"/>
    </g>
  </svg>

  <svg class="abs" style="left:120px;top:97px" width="190" height="190" viewBox="0 0 190 190">
    <path d="M95 2 L112 18 134 10 143 32 166 34 164 57 184 70 172 90 184 110 166 125 166 148 143 152 134 175 112 168 95 185 78 168 56 175 47 152 24 148 24 125 6 110 18 90 6 70 26 57 24 34 47 32 56 10 78 18Z" fill="var(--red)"/>
    <text x="95" y="52" text-anchor="middle" fill="#fff" font-family="Montserrat,sans-serif" font-size="20" letter-spacing="4">OVER</text>
    <text x="80" y="124" text-anchor="middle" fill="var(--yellow)" font-family="Poppins,sans-serif" font-weight="800" font-size="76">50</text>
    <text x="140" y="88" text-anchor="middle" fill="#fff" font-family="Montserrat,sans-serif" font-size="13" letter-spacing="1">YEARS</text>
    <text x="95" y="148" text-anchor="middle" fill="#fff" font-family="Montserrat,sans-serif" font-size="17">EXPERIENCE</text>
  </svg>

  <div class="headline kicker">COMMERCIAL</div>
  <div class="headline title">SITE CONSTRUCTION</div>
  <div class="headline subtitle">FARM &amp; RANCH PROJECTS<br>TO OILFIELD SERVICES</div>
  <div class="rule"></div>

  <div class="headline seg-head commercial-head">FOR COMMERCIAL<br><span class="hl">CUSTOMERS</span></div>
  <div class="tag tag-commercial">WE BUILD</div>

  <div class="service" style="left:645px;top:437px">
    <svg width="52" height="52" viewBox="0 0 52 52"><rect x="1.5" y="1.5" width="49" height="49" rx="4" fill="var(--yellow)" stroke="#fff" stroke-width="2"/><path d="M14 14h16v24H14zM20 34l14-14 4 4-14 14z" fill="none" stroke="#222" stroke-width="2"/></svg>
    <span>Building<br>Pads</span>
  </div>
  <div class="service" style="left:815px;top:437px">
    <svg width="52" height="52" viewBox="0 0 52 52"><rect x="1.5" y="1.5" width="49" height="49" rx="4" fill="var(--yellow)" stroke="#fff" stroke-width="2"/><path d="M18 12 12 40M34 12l6 28M26 14v5M26 24v5M26 34v5" fill="none" stroke="#222" stroke-width="2"/></svg>
    <span>Pavement</span>
  </div>
  <div class="service" style="left:645px;top:515px">
    <svg width="52" height="52" viewBox="0 0 52 52"><rect x="1.5" y="1.5" width="49" height="49" rx="4" fill="var(--yellow)" stroke="#fff" stroke-width="2"/><path d="M12 32h26v6H12zM18 32V22h12l4 10M14 44h24" fill="none" stroke="#222" stroke-width="2"/><circle cx="18" cy="41" r="2" fill="#222"/><circle cx="32" cy="41" r="2" fill="#222"/></svg>
    <span>Site<br>Clearing</span>
  </div>
  <div class="service" style="left:815px;top:515px">
    <svg width="52" height="52" viewBox="0 0 52 52"><rect x="1.5" y="1.5" width="49" height="49" rx="4" fill="var(--yellow)" stroke="#fff" stroke-width="2"/><path d="M26 10v20M19 23l7 7 7-7M10 36h32M10 42h32" fill="none" stroke="#222" stroke-width="2"/></svg>
    <span>Soil<br>Stabilization</span>
  </div>

  <p class="intro"><span class="hl">Over 50 years of experience in the industry,</span><br>we have what it takes to help you develop<br>your land for your long or short term goals.</p>

  <div class="headline seg-head farm-head">FOR FARMERS &amp;<br><span class="hl">RANCHERS</span></div>
  <div class="tag tag-farm">WE BUILD</div>

  <div class="farm-item" style="left:600px;top:819px">
    <svg width="70" height="70" viewBox="0 0 70 70"><circle cx="35" cy="35" r="33" fill="var(--yellow)" stroke="#222" stroke-width="1.5"/><path d="M16 40c6-8 32-8 38 0-6 6-32 6-38 0zM24 32l6-8 5 6 5-7 6 9" fill="none" stroke="#222" stroke-width="2"/></svg>
    <div style="margin-top:16px">Lakes</div>
  </div>
  <div class="divider" style="left:724px"></div>
  <div class="farm-item" style="left:733px;top:819px">
    <svg width="70" height="70" viewBox="0 0 70 70"><circle cx="35" cy="35" r="33" fill="var(--yellow)" stroke="#222" stroke-width="1.5"/><path d="M16 42c5-7 33-7 38 0-5 6-33 6-38 0zM28 30v-8M35 32v-12M42 30v-8" fill="none" stroke="#222" stroke-width="2"/></svg>
    <div style="margin-top:18px">Ponds</div>
  </div>
  <div class="divider" style="left:868px"></div>
  <div class="farm-item" style="left:867px;top:819px">
    <svg width="70" height="70" viewBox="0 0 70 70"><circle cx="35" cy="35" r="33" fill="var(--yellow)" stroke="#222" stroke-width="1.5"/><path d="M18 52l22-22M36 26l8 8 8-10-6-6zM20 30l4 4M24 22l3 5" fill="none" stroke="#222" stroke-width="2"/></svg>
    <div style="margin-top:18px">Brush<br>Clearing</div>
  </div>

  <div class="snap" style="left:78px;top:712px;width:218px;height:145px;transform:rotate(-1.5deg)">
    <div class="shot" role="img" aria-label="Freshly graded pond site with trees and a laser level" style="background:linear-gradient(#7fb0dc 0%,#d3e3ee 38%,#4e6a36 46%,#5a4a39 62%,#3d3328 100%)"></div>
    <div class="caption">LAZER - POND</div>
  </div>
  <div class="snap" style="left:328px;top:707px;width:215px;height:145px;transform:rotate(-1deg)">
    <div class="shot" role="img" aria-label="Aerial view of a paved lot beside a large warehouse" style="background:linear-gradient(160deg,#7d8a5c 0%,#cfcdc4 25%,#e9e7e1 55%,#b8b3a8 100%)"></div>
    <div class="caption">CEDAR - FOOD BANK</div>
  </div>
  <div class="snap" style="left:83px;top:872px;width:220px;height:150px;transform:rotate(-1deg)">
    <div class="shot" role="img" aria-label="Aerial view of a cleared building pad next to a road" style="background:linear-gradient(135deg,#4f5a40 0%,#5e5a4e 30%,#8a867a 60%,#c9c6bb 100%)"></div>
    <div class="caption">SOMERSET</div>
  </div>
  <div class="snap" style="left:333px;top:869px;width:225px;height:150px;transform:rotate(-1.5deg)">
    <div class="shot" role="img" aria-label="Finished pond with green bank and trees behind" style="background:linear-gradient(#9fc0dc 0%,#5f7d4a 30%,#5b7d95 44%,#7fa446 62%,#3e5c2a 100%)"></div>
    <div class="caption">TURKEY POND</div>
  </div>

  <div class="contact-label">CONTACT US</div>
  <div class="phone">
    <svg width="18" height="18" viewBox="0 0 18 18"><circle cx="9" cy="9" r="9" fill="var(--ink)"/><path d="M6 4.5l2 2-1 1.5c.6 1.3 1.5 2.2 2.8 2.8l1.5-1 2 2-1.3 1.6C8.5 13.2 4.8 9.5 4.6 5.8z" fill="var(--yellow)"/></svg>
    512.404.7730
  </div>

  <div class="estimate">GET AN ESTIMATE</div>
  <div class="web">
    <svg width="13" height="13" viewBox="0 0 14 14"><circle cx="7" cy="7" r="6" fill="none" stroke="var(--yellow)" stroke-width="1.5"/><path d="M1 7h12M7 1c3 3 3 9 0 12M7 1c-3 3-3 9 0 12" fill="none" stroke="var(--yellow)" stroke-width="1.2"/></svg>
    <span>www.<span class="hl">pendrowgrading</span>.com</span>
  </div>

  <div class="brand"><span class="mark"></span><span>Pendrow<br>Grading</span></div>
</div>
</body>
</html>
```